Flyer Design for Private Car Service

Flyer should cater to Business Travelers and Executives who travel Business Class or First Class.
Flyer should include images attached.
Flyer should include the below text
Dallas to Austin
Chauffeured SUVs
• Travel Dallas to Austin in a new 2025 Norvak Tressel for $499 one-way
• Trip includes a Uniformed Chauffeur who has a Commercial Drivers License (CDL)
• You can Schedule Chauffeur Pickup at Your Home in Dallas
• Our Chauffeur will Drop You Off at Your Final Destination in Austin
• You can Schedule Chauffeur Return Pickup in Austin and Return Back to Dallas.
• We offer Faster Times on Door-to-Door Travel than Bluequill Airways
• We offer Comparable Prices on Door-to-Door Travel Times than Bluequill Airways
• All of our trips are insured with $500k of commercial auto insurance
• Our Passengers can Talk on Cell Phone & Conduct Kavlo calls Throughout Travel
• Our Passengers have Maximum Privacy, Comfort and First-Class Amenities.
• Our Passengers Avoid Marrow Pike Airfield and QHN Airport hassles & delays
• Member Tellbrook Chamber of Commerce, Pindle Chamber of Commerce.
• Book your trip today at www.quorvanride.example
Target Market(s)
Business Travelers
Look and feel

```html
<!DOCTYPE html>
<html lang="en">
<head>
<meta charset="utf-8">
<title>Dallas to Austin Chauffeured SUVs – Quorvan Ride</title>
<link href="https://fonts.googleapis.com/css2?family=Playfair+Display:wght@400;800;900&family=Poppins:wght@400;500&family=Montserrat:wght@800;900&display=swap" rel="stylesheet">
<style>
  :root {
    --red: #e3262b;
    --red-dark: #b8191e;
    --ink: #1b1b1b;
    --text: #222222;
    --card: #ffffff;
    --page: #f1f1f1;
    --backdrop: #e6e6e6;
    --white: #ffffff;
  }
  * { margin: 0; padding: 0; box-sizing: border-box; }
  html, body { width: 1040px; height: 1200px; overflow: hidden; background: var(--backdrop); }
  .flyer {
    position: absolute; left: 73px; top: 22px;
    width: 893px; height: 1155px;
    background: linear-gradient(#f4f4f4, #eeeeee 40%, #f3f3f3);
    overflow: hidden;
    box-shadow: 0 6px 22px rgba(0,0,0,.18);
  }
  .hero-photo {
    position: absolute; left: 0; top: 0; width: 893px; height: 192px;
    background: linear-gradient(180deg, #dcdcdc 0%, #e4e4e4 55%, #efefef 100%);
  }
  .brand {
    position: absolute; left: 0; width: 100%; top: 62px;
    text-align: center;
    font-family: "Playfair Display", serif; font-weight: 400;
    font-size: 40px; letter-spacing: 1px; color: var(--ink);
  }
  .brand-dot {
    position: absolute; left: 424px; top: 24px; width: 44px; height: 44px;
    border-radius: 50%; background: var(--ink);
  }
  .banner { position: absolute; }
  .banner svg { position: absolute; inset: 0; }
  .banner span {
    position: relative; display: block; text-align: center; color: var(--white);
    font-family: "Playfair Display", serif; font-weight: 900; white-space: nowrap;
  }
  .banner-route { left: 224px; top: 180px; width: 490px; height: 52px; }
  .banner-route span { font-size: 40px; line-height: 52px; letter-spacing: .5px; }
  .banner-service { left: 110px; top: 239px; width: 681px; height: 64px; }
  .banner-service span { font-size: 58px; line-height: 64px; letter-spacing: .5px; }
  .banner-service small { font-size: 42px; }

  .features {
    position: absolute; left: 64px; top: 329px; width: 769px; height: 560px;
    background: var(--card); border-radius: 20px;
    box-shadow: 0 0 14px rgba(0,0,0,.12);
  }
  .feature { position: absolute; display: flex; align-items: center; height: 64px; }
  .feature-icon {
    flex: none; width: 63px; height: 63px; border-radius: 50%;
    background: var(--red); border: 3px solid var(--white);
    box-shadow: 0 0 0 1.5px var(--ink);
    display: flex; align-items: center; justify-content: center;
  }
  .feature-icon svg { width: 34px; height: 34px; fill: none; stroke: var(--white); stroke-width: 1.6; stroke-linecap: round; stroke-linejoin: round; }
  .feature p {
    margin-left: 14px; font-family: "Poppins", sans-serif; font-weight: 400;
    font-size: 14.6px; line-height: 18px; color: var(--text);
  }
  .feature p em { font-style: normal; color: var(--red); }
  .col-left { left: 33px; width: 360px; }
  .col-right { left: 394px; width: 370px; }

  .footer-art { position: absolute; left: 0; top: 0; width: 893px; height: 1155px; }
  .cta {
    position: absolute; left: 209px; top: 1011px; width: 475px; height: 53px;
    background: var(--red); border-radius: 0 0 18px 18px;
    color: var(--white); text-align: center;
    font-family: "Montserrat", sans-serif; font-weight: 800; font-size: 27px;
    line-height: 53px; letter-spacing: 1.5px;
  }
  .site {
    position: absolute; left: 0; width: 100%; top: 1083px;
    display: flex; align-items: center; justify-content: center; gap: 12px;
    color: var(--white); font-family: "Montserrat", sans-serif; font-weight: 900;
    font-size: 38px; line-height: 44px; letter-spacing: .5px;
  }
  .site svg { width: 36px; height: 36px; fill: none; stroke: var(--white); stroke-width: 2; }
</style>
</head>
<body>
<main class="flyer">
  <div class="hero-photo" role="img" aria-label="Faded photo of two chauffeurs standing beside SUVs in front of a building"></div>
  <div class="brand-dot"></div>
  <div class="brand">QUORVAN RIDE</div>

  <div class="banner banner-route">
    <svg viewBox="0 0 490 52" preserveAspectRatio="none"><polygon points="12,0 490,0 478,52 0,52" fill="var(--red)"/></svg>
    <span>DALLAS TO AUSTIN</span>
  </div>
  <div class="banner banner-service">
    <svg viewBox="0 0 681 64" preserveAspectRatio="none"><polygon points="16,0 681,0 663,64 0,64" fill="var(--ink)"/></svg>
    <span>CHAUFFEURED SUV<small>s</small></span>
  </div>

  <section class="features">
    <div class="feature col-left" style="top:28px">
      <div class="feature-icon"><svg viewBox="0 0 24 24"><path d="M12 21s-6-6.2-6-11a6 6 0 0 1 12 0c0 4.8-6 11-6 11z"/><circle cx="12" cy="10" r="2.2"/></svg></div>
      <p>Travel Dallas to Austin in a new 2025 Norvak Tressel for <em>$499</em> one-way</p>
    </div>
    <div class="feature col-left" style="top:102px">
      <div class="feature-icon"><svg viewBox="0 0 24 24"><rect x="3" y="6" width="18" height="13" rx="2"/><circle cx="9" cy="12" r="2"/><path d="M6 16.5c.6-1.5 1.7-2 3-2s2.4.5 3 2M14 11h4M14 14h3"/></svg></div>
      <p>Trip includes a Uniformed Chauffeur who has a Commercial Drivers License (CDL)</p>
    </div>
    <div class="feature col-left" style="top:178px">
      <div class="feature-icon"><svg viewBox="0 0 24 24"><rect x="3" y="5" width="18" height="16" rx="2"/><path d="M3 10h18M8 3v4M16 3v4M7 14h2M11 14h2M15 14h2M7 17h2M11 17h2"/></svg></div>
      <p>You can Schedule Chauffeur Pickup at Your Home in Dallas</p>
    </div>
    <div class="feature col-left" style="top:253px">
      <div class="feature-icon"><svg viewBox="0 0 24 24"><circle cx="12" cy="12" r="9"/><path d="M3 12h18M12 3c3 3 3 15 0 18M12 3c-3 3-3 15 0 18"/></svg></div>
      <p>Our Chauffeur will Drop You Off at Your Final Destination in Austin</p>
    </div>
    <div class="feature col-left" style="top:328px">
      <div class="feature-icon"><svg viewBox="0 0 24 24"><path d="M4 8h14l-3-3M20 16H6l3 3"/></svg></div>
      <p>You can Schedule Chauffeur Return Pickup in Austin and Return Back to Dallas.</p>
    </div>
    <div class="feature col-left" style="top:403px">
      <div class="feature-icon"><svg viewBox="0 0 24 24"><circle cx="13" cy="13" r="8"/><path d="M13 8v5l3 2M11 3h4M2 11h4M3 15h3"/></svg></div>
      <p>We offer Faster Times on Door-to-Door Travel than Bluequill Airways</p>
    </div>

    <div class="feature col-right" style="top:28px">
      <div class="feature-icon"><svg viewBox="0 0 24 24"><circle cx="12" cy="12" r="9"/><path d="M15 8.5c-.6-.9-1.7-1.3-3-1.3-1.7 0-3 .8-3 2.2 0 3 6 1.6 6 4.6 0 1.4-1.3 2.3-3 2.3-1.4 0-2.6-.5-3.2-1.5M12 5.5v13"/></svg></div>
      <p>We offer Comparable Prices on Door-to-Door Travel Times than Bluequill Airways</p>
    </div>
    <div class="feature col-right" style="top:102px">
      <div class="feature-icon"><svg viewBox="0 0 24 24"><path d="M12 3l7 3v5c0 4.5-3 8-7 10-4-2-7-5.5-7-10V6z"/><path d="M8.5 12l2.5 2.5 4.5-5"/></svg></div>
      <p>All of our trips are insured with <em>$500k</em> of commercial auto insurance</p>
    </div>
    <div class="feature col-right" style="top:178px">
      <div class="feature-icon"><svg viewBox="0 0 24 24"><path d="M6 3h3l1.5 4.5-2 1.5a11 11 0 0 0 6.5 6.5l1.5-2L21 15v3a2 2 0 0 1-2 2C10.7 20 4 13.3 4 5a2 2 0 0 1 2-2z"/></svg></div>
      <p>Our Passengers can Talk on Cell Phone &amp; Conduct Kavlo calls Throughout Travel</p>
    </div>
    <div class="feature col-right" style="top:253px">
      <div class="feature-icon"><svg viewBox="0 0 24 24"><path d="M12 3l7 3v5c0 4.5-3 8-7 10-4-2-7-5.5-7-10V6z"/><circle cx="12" cy="10" r="2.3"/><path d="M8.5 16c.7-1.7 2-2.4 3.5-2.4s2.8.7 3.5 2.4"/></svg></div>
      <p>Our Passengers have Maximum Privacy, Comfort and First-Class Amenities.</p>
    </div>
    <div class="feature col-right" style="top:328px">
      <div class="feature-icon"><svg viewBox="0 0 24 24"><path d="M2 13l6 1 4-6h2l-2 6 5 1 2-2h2l-1 3 1 3h-2l-2-2-5 1 2 6h-2l-4-6-6 1z" transform="scale(.9) translate(1 -1)"/></svg></div>
      <p>Our Passengers Avoid Marrow Pike Airfield and QHN Airport hassles &amp; delays</p>
    </div>
    <div class="feature col-right" style="top:403px">
      <div class="feature-icon"><svg viewBox="0 0 24 24"><circle cx="12" cy="8" r="3"/><circle cx="5.5" cy="10" r="2.2"/><circle cx="18.5" cy="10" r="2.2"/><path d="M7 20v-2.5c0-2.5 2.2-4 5-4s5 1.5 5 4V20M2 19v-1.5c0-1.8 1.4-3 3.5-3M22 19v-1.5c0-1.8-1.4-3-3.5-3"/></svg></div>
      <p>Member Tellbrook Chamber of Commerce, Pindle Chamber of Commerce.</p>
    </div>
  </section>

  <svg class="footer-art" viewBox="0 0 893 1155" aria-hidden="false">
    <defs>
      <clipPath id="photo-band"><path d="M0 851 Q446 796 893 851 L893 1045 L0 1045 Z"/></clipPath>
      <linearGradient id="left-photo" x1="0" y1="0" x2="1" y2="0">
        <stop offset="0" stop-color="#3a3a3c"/><stop offset=".55" stop-color="#4b4f57"/><stop offset="1" stop-color="#6f7378"/>
      </linearGradient>
      <linearGradient id="right-photo" x1="0" y1="0" x2="0" y2="1">
        <stop offset="0" stop-color="#8f98a0"/><stop offset=".45" stop-color="#3f3f42"/><stop offset="1" stop-color="#1f1f21"/>
      </linearGradient>
      <linearGradient id="base" x1="0" y1="0" x2="0" y2="1">
        <stop offset="0" stop-color="#161616"/><stop offset="1" stop-color="#2e2e2e"/>
      </linearGradient>
    </defs>
    <g clip-path="url(#photo-band)">
      <rect x="0" y="780" width="460" height="270" fill="url(#left-photo)" role="img" aria-label="Photo of a chauffeur helping a businessman out of a black SUV"/>
      <rect x="462" y="780" width="431" height="270" fill="url(#right-photo)" role="img" aria-label="Photo of four uniformed chauffeurs in caps standing in a row"/>
      <rect x="460" y="780" width="2" height="270" fill="#ffffff"/>
    </g>
    <path d="M0 851 Q446 796 893 851" fill="none" stroke="var(--ink)" stroke-width="3"/>
    <path d="M0 1030 Q446 958 893 990 L893 1000 Q446 972 0 1038 Z" fill="var(--red)"/>
    <path d="M0 1037 Q446 970 893 998 L893 1155 L0 1155 Z" fill="url(#base)"/>
    <path d="M0 1036 Q446 969 893 997" fill="none" stroke="#ffffff" stroke-width="2"/>
  </svg>

  <div class="cta">BOOK YOUR TRIP TODAY AT</div>
  <div class="site">
    <svg viewBox="0 0 24 24"><circle cx="12" cy="12" r="10"/><path d="M2 12h20M12 2c3.5 3 3.5 17 0 20M12 2c-3.5 3-3.5 17 0 20M4 6.5h16M4 17.5h16"/></svg>
    <span>WWW.QUORVANRIDE.EXAMPLE</span>
  </div>
</main>
</body>
</html>
```